NEW Modern Sleek Business Card for VR Language Startup

Our startup is using VR to lead the next wave of world language education. We need a two-sided business card that introduces the larger organization (Brightloom Language Inc) and our contact info on one side and shows the product, Glimwoorld, on the other side.

Side 1 (contact info)= Brightloom Logo and Contact info (name, title, phone, email)

Side 2 (product)= Glimworld logo, text, and website
Text= Culturally Immersive Language Learning Games
Website= www.glimworld-play.com

Target Market(s)

Education, Technology

Contact Information for Business Card

Contact info will be updated upon approval of the design. For now, put this as a placeholder.

Perry Dunmore
Founder & CEO
pdunmore@quillpost-mail.net
(555)-014-2286

Font styles to use
Other font styles liked:
• Gibson and Century Gothic are the brand fonts

Requirements
Nice to have
• I would love to see cohesion between the design and colors of the two logos. I have attached a few business card designs that I like, so you can get a feel for my preferred style.

```html
<!DOCTYPE html>
<html lang="en">
<head>
<meta charset="utf-8">
<title>Brightloom Language – Business Card</title>
<link rel="stylesheet" href="https://fonts.googleapis.com/css2?family=Questrial&family=Montserrat:wght@600;700&display=swap">
<style>
  :root {
    --bg: #d9d9db;
    --card: #151515;
    --card-edge: #222222;
    --white: #ffffff;
    --grey-word: #4a4a4a;
    --blue: #4a8cf2;
    --cyan: #1fd8ee;
    --violet: #7a5cf0;
    --orange: #f5a630;
    --red: #ff3340;
    --magenta: #c446a0;
  }
  * { box-sizing: border-box; margin: 0; padding: 0; }
  html, body { width: 1200px; height: 1200px; overflow: hidden; }
  body {
    background: var(--bg);
    display: flex;
    flex-direction: column;
    align-items: center;
    justify-content: center;
    gap: 44px;
    font-family: "Questrial", "Century Gothic", sans-serif;
  }
  .card {
    position: relative;
    width: 900px;
    height: 514px;
    border-radius: 28px;
    background: linear-gradient(135deg, #0c0c0c 0%, var(--card) 55%, var(--card-edge) 100%);
    overflow: hidden;
    box-shadow: 0 18px 40px rgba(0,0,0,.35);
  }

  /* Product side */
  .product {
    display: flex;
    flex-direction: column;
    align-items: center;
    justify-content: center;
  }
  .product-brand {
    display: flex;
    align-items: center;
    gap: 18px;
  }
  .product-brand .dot {
    width: 54px; height: 54px; border-radius: 50%;
    background: var(--blue);
  }
  .product-name {
    font-size: 78px;
    color: var(--grey-word);
    letter-spacing: 1px;
  }
  .tagline {
    margin-top: 10px;
    font-size: 25px;
    color: var(--blue);
    letter-spacing: .5px;
  }
  .website {
    margin-top: 54px;
    font-family: "Montserrat", sans-serif;
    font-weight: 700;
    font-size: 20px;
    color: var(--blue);
    letter-spacing: .5px;
  }

  /* Contact side */
  .contact .info {
    position: absolute;
    left: 70px;
    top: 60px;
  }
  .company {
    display: flex;
    align-items: center;
    gap: 14px;
  }
  .company .dot {
    width: 34px; height: 34px; border-radius: 50%;
    background: var(--red);
  }
  .company-name {
    font-size: 34px;
    color: var(--white);
    letter-spacing: 3px;
  }
  .person-name {
    margin-top: 64px;
    font-family: "Montserrat", sans-serif;
    font-weight: 700;
    font-size: 30px;
    color: var(--white);
  }
  .person-title {
    margin-top: 4px;
    font-size: 19px;
    color: var(--white);
  }
  .rule {
    width: 42px; height: 2px;
    background: var(--red);
    margin: 14px 0 18px;
  }
  .contact-line {
    display: flex;
    align-items: center;
    gap: 12px;
    font-size: 18px;
    color: var(--white);
    margin-bottom: 10px;
  }
  .contact-line svg { width: 20px; height: 20px; flex: none; }
  .feature-art {
    position: absolute;
    right: 0;
    bottom: 0;
    width: 380px;
    height: 300px;
    border-top-left-radius: 160px;
    background: linear-gradient(160deg, var(--orange) 0%, var(--red) 45%, var(--magenta) 75%, var(--violet) 100%);
  }
</style>
</head>
<body>

  <section class="card product">
    <div class="product-brand">
      <span class="dot"></span>
      <span class="product-name">Glimworld</span>
    </div>
    <p class="tagline">Culturally Immersive Language Learning Games</p>
    <p class="website">www.glimworld-play.com</p>
  </section>

  <section class="card contact">
    <div class="info">
      <div class="company">
        <span class="dot"></span>
        <span class="company-name">BRIGHTLOOM LANGUAGE</span>
      </div>
      <p class="person-name">PERRY DUNMORE</p>
      <p class="person-title">President</p>
      <div class="rule"></div>
      <p class="contact-line">
        <svg viewBox="0 0 20 20" aria-hidden="true">
          <rect x="2" y="5" width="16" height="11" rx="1.5" fill="none" stroke="#ff3340" stroke-width="1.8"/>
          <path d="M2.5 6 L10 11.5 L17.5 6" fill="none" stroke="#ff3340" stroke-width="1.8"/>
        </svg>
        pdunmore@quillpost-mail.net
      </p>
      <p class="contact-line">
        <svg viewBox="0 0 20 20" aria-hidden="true">
          <path d="M5 2.5 L8 6 L6.3 8 C7.3 10.3 9.7 12.7 12 13.7 L14 12 L17.5 15 L15.5 17.5 C9 17 3 11 2.5 4.5 Z" fill="#ff3340"/>
        </svg>
        (555)-014-2286
      </p>
    </div>
    <div class="feature-art" role="img" aria-label="Large gradient brand decoration in orange, red and violet"></div>
  </section>

</body>
</html>
```